Business Card Design Project

Business Card
We are rebranding with a new logo
Industry/Entity Type
Business
Contact Information for Business Card
Dennis Morvale +61 487215963 dennis@quorv.com.au P.O. Box 872 Fernlow QLD 4309
Requirements
Must have
- Logo

```html
<!DOCTYPE html>
<html lang="en">
<head>
<meta charset="utf-8">
<title>Quorv International – Business Card</title>
<link rel="stylesheet" href="https://fonts.googleapis.com/css2?family=Arimo:wght@400;700&display=swap">
<style>
  :root {
    --backdrop: #2a2e33;
    --card: #ffffff;
    --brand-blue: #1a8fc2;
    --deep-blue: #1f6f98;
    --light-blue: #2aa6da;
    --brand-orange: #f07d1e;
    --text-dark: #4a4d50;
    --text-muted: #6d7073;
  }
  html, body {
    margin: 0;
    padding: 0;
    width: 1200px;
    height: 902px;
    overflow: hidden;
    background: var(--backdrop);
    font-family: "Arimo", Arial, sans-serif;
  }
  .card {
    position: absolute;
    left: 100px;
    top: 151px;
    width: 1000px;
    height: 600px;
    background: var(--card);
    border-radius: 34px;
    overflow: hidden;
  }
  .card__accent {
    position: absolute;
    left: 0;
    right: 0;
    bottom: 72px;
    height: 8px;
    background: var(--brand-orange);
  }
  .card__band {
    position: absolute;
    left: 0;
    right: 0;
    bottom: 0;
    height: 64px;
    background: linear-gradient(90deg, var(--deep-blue), var(--brand-blue) 60%, var(--light-blue));
  }
  .brand {
    position: absolute;
    right: 70px;
    top: 72px;
    display: flex;
    align-items: center;
    gap: 14px;
  }
  .brand__dot {
    width: 26px;
    height: 26px;
    border-radius: 50%;
    background: var(--brand-blue);
  }
  .brand__name {
    font-size: 38px;
    font-weight: 700;
    color: var(--brand-blue);
    letter-spacing: 0.5px;
  }
  .person {
    position: absolute;
    left: 88px;
    top: 176px;
  }
  .person__name {
    margin: 0;
    font-size: 44px;
    font-weight: 700;
    color: var(--brand-blue);
    line-height: 1;
  }
  .person__role {
    margin: 8px 0 0 24px;
    font-size: 21px;
    color: var(--text-muted);
  }
  .contact {
    position: absolute;
    left: 96px;
    top: 290px;
    margin: 0;
    padding: 0;
    list-style: none;
    font-size: 27px;
    color: var(--text-dark);
    line-height: 1.2;
  }
  .contact__item {
    display: flex;
    align-items: flex-start;
    gap: 18px;
  }
  .contact__item--address { margin-bottom: 36px; }
  .contact__item--phone { margin-bottom: 6px; }
  .contact__icon {
    width: 26px;
    height: 26px;
    flex: none;
    margin-top: 4px;
    fill: var(--brand-blue);
  }
</style>
</head>
<body>
  <article class="card">
    <div class="card__accent" aria-hidden="true"></div>
    <div class="card__band" aria-hidden="true"></div>

    <div class="brand">
      <span class="brand__dot"></span>
      <span class="brand__name">Quorv International</span>
    </div>

    <header class="person">
      <h1 class="person__name">Dennis Morvale</h1>
      <p class="person__role">Owner</p>
    </header>

    <ul class="contact">
      <li class="contact__item contact__item--address">
        <svg class="contact__icon" viewBox="0 0 24 24" aria-hidden="true"><path d="M12 3 2 12h3v9h5v-6h4v6h5v-9h3z"/></svg>
        <span>P.O. Box 872<br>Fernlow QLD 4309</span>
      </li>
      <li class="contact__item contact__item--phone">
        <svg class="contact__icon" viewBox="0 0 24 24" aria-hidden="true"><path d="M7 1h10a2 2 0 0 1 2 2v18a2 2 0 0 1-2 2H7a2 2 0 0 1-2-2V3a2 2 0 0 1 2-2zm0 3v14h10V4zm5 15.5a1.2 1.2 0 1 0 0 2.4 1.2 1.2 0 0 0 0-2.4z"/></svg>
        <span>+61 487215963</span>
      </li>
      <li class="contact__item contact__item--email">
        <svg class="contact__icon" viewBox="0 0 24 24" aria-hidden="true"><path d="M2 5h20v14H2zm2 2v.5l8 5.5 8-5.5V7zm0 3v7h16v-7l-8 5.5z"/></svg>
        <span>dennis@quorv.com.au</span>
      </li>
    </ul>
  </article>
</body>
</html>
```